Anzeigengestaltung für eine Hausarztpraxis
Zielgruppe
Wir sind eine Hausarztpraxis mit zwei Standorten und suchen eine Ärztin oder einen Arzt zur Anstellung in der klassischen Hausarzt Medizin am Standort Mattwil
Aufgabenstellung
Bitte beachtet den Text im Anhang, der ist schon vorgegeben. (Anzeigentext)
Wir suchen ein ruhiges, hochwertiges Layout für eine Stellenanzeige einer Hausarztpraxis in einem historischen Gebäude.
Der Text steht im Vordergrund, das Design soll zurückhaltend, klar und wertig sein.
Bitte keine Icons, keine bunten Farben, keine verspielten Elemente.
Gerne viel Weissraum, klare Typografie, ruhige Anmutung.
Schrift: Garamond für den Fliesstext (bereits gewählt).
Das Layout soll sowohl als PDF wie auch online funktionieren.
Optional: ein sehr dezentes grafisches Element oder eine ruhige Bildanmutung (z. B. Struktur, Licht, Architekturdetail).

```html
<!DOCTYPE html>
<html lang="de">
<head>
<meta charset="utf-8">
<title>Stellenanzeige Hausarztpraxis Mattwil</title>
<link href="https://fonts.googleapis.com/css2?family=EB+Garamond:ital,wght@0,400;0,600;0,700;1,400&display=swap" rel="stylesheet">
<style>
  :root {
    --frame: #e9e9eb;
    --paper: #ffffff;
    --ink: #2e302d;
    --ink-strong: #24291f;
    --photo-light: #f3f0ea;
    --photo-warm: #c9b9a6;
    --accent-dot: #24291f;
  }
  * { margin: 0; padding: 0; box-sizing: border-box; }
  html, body { width: 902px; height: 1200px; overflow: hidden; background: var(--frame); }
  body { font-family: "EB Garamond", Garamond, serif; color: var(--ink); }
  .ad {
    position: absolute; left: 15px; top: 20px; width: 872px; height: 1160px;
    background: var(--paper);
  }
  .ad-photo {
    position: absolute; left: 50px; top: 31px; width: 787px; height: 236px;
    background: linear-gradient(90deg, var(--photo-warm) 0%, #d8cbbd 16%, var(--photo-light) 34%, #fbfaf7 55%, #eeebe5 78%, #cdbfb0 90%, var(--photo-warm) 100%);
  }
  .ad-photo::after {
    content: ""; position: absolute; left: 0; right: 0; bottom: 0; height: 60px;
    background: linear-gradient(180deg, rgba(140,122,104,0) 0%, rgba(140,122,104,0.35) 100%);
  }
  .block { position: absolute; white-space: nowrap; }
  .col-left { left: 46px; }
  .col-right { left: 460px; }
  .headline {
    font-size: 21px; font-weight: 700; line-height: 25.5px; color: var(--ink-strong);
    letter-spacing: 0.3px;
  }
  .subhead {
    font-size: 17.5px; font-weight: 700; line-height: 22px; color: var(--ink-strong);
    letter-spacing: 0.2px;
  }
  .lead { font-size: 17px; font-style: italic; line-height: 24.6px; }
  .body { font-size: 17px; line-height: 24.6px; letter-spacing: 0.15px; }
  .contact-mail { font-size: 15.5px; font-weight: 700; color: var(--ink-strong); }
  .address { font-size: 15px; line-height: 19.8px; font-style: normal; }
  .address .firm { font-weight: 700; color: var(--ink-strong); }
  .brand { display: flex; align-items: center; gap: 10px; }
  .brand-dot { width: 14px; height: 14px; border-radius: 50%; background: var(--accent-dot); }
  .brand-name { font-size: 18px; font-weight: 700; color: var(--ink-strong); }
</style>
</head>
<body>
  <main class="ad">
    <div class="ad-photo" role="img" aria-label="Blick durch eine Tür in einen hellen, holzvertäfelten Behandlungsraum mit Liege, Schreibtisch, Bildschirm und zwei Drahtstühlen"></div>

    <h1 class="block col-left headline" style="top:290px;">Hausarztmedizin mit Tiefe – dort, wo man<br>noch echte Grundversorgung lebt</h1>

    <p class="block col-left lead" style="top:389px;">Ein Ort, der trägt. Ein Team, das bleibt. Eine Arbeit, die<br>Wertschätzung hat.</p>

    <p class="block col-left body" style="top:463px;">Manche Orte verändern die Art, wie man arbeitet.<br>Unsere Praxis in Mattwil ist so ein Ort.</p>

    <p class="block col-left body" style="top:536px;">In einem historischen Gebäude gelegen, mit<br>grosszügigem Ambiente, warmen Vertäfelungen und<br>kunstvoller Wandbemalung, entstehen hier<br>Behandlungsräume von Ruhe und Würde. Kein<br>steriler Praxisalltag, sondern ein Ort, der Gespräche<br>trägt und medizinische Arbeit unterstützt.</p>

    <p class="block col-left body" style="top:709px;">Für diesen besonderen Ort suchen wir eine<br>Hausärztin oder einen Hausarzt, die oder der nicht<br>einfach einen Arbeitsplatz sucht, sondern einen Platz,<br>an dem Medizin menschlich sein darf.</p>

    <p class="block col-left contact-mail" style="top:892px;">E-Mail: Helga.Weißmoor@praxis-lindenhof.ch</p>

    <address class="block col-left address" style="top:920px;">
      <span class="firm">Arztpraxis Lindenhof</span><br>
      Mühlegasse 7<br>
      4718 Mattwil<br>
      Tel: 0621234578
    </address>

    <div class="block col-left brand" style="top:1060px;">
      <span class="brand-dot"></span>
      <span class="brand-name">Arztpraxis Lindenhof</span>
    </div>

    <h2 class="block col-right subhead" style="top:292px;">Ein Team mit Haltung</h2>
    <p class="block col-right body" style="top:340px;">Sie arbeiten in einem freundlichen, über Jahre<br>gewachsenen Team mit hoher personeller Kontinuität<br>und geringer Fluktuation.</p>

    <h2 class="block col-right subhead" style="top:439px;">Zeit für gute Medizin</h2>
    <p class="block col-right body" style="top:487px;">Unsere Patientinnen und Patienten sind überwiegend<br>gut bis sehr gut situiert, wertschätzend und<br>therapieoffen. Das ermöglicht ruhiges, strukturiertes<br>Arbeiten mit Fokus auf Qualität, Beziehung und<br>nachhaltige Behandlung.</p>

    <h2 class="block col-right subhead" style="top:636px;">Und sonst?</h2>
    <p class="block col-right body" style="top:684px;">Der Praxisalltag ist klar strukturiert, ruhig und<br>verlässlich. Geregelte und in Abstimmung flexible<br>Arbeitszeiten ohne Wochenend- oder Nachtdienste,<br>eine sehr gute leistungsbezogene Vergütung sowie ein<br>respektvoller, wertschätzender Umgang auf<br>Augenhöhe schaffen ein Umfeld, in dem man sich<br>auf die medizinische Arbeit konzentrieren und<br>langfristig wohlfühlen kann.</p>

    <p class="block col-right body" style="top:906px;">Wir freuen uns über eine unkomplizierte<br>Kontaktaufnahme per E-Mail oder Telefon – gerne<br>auch ganz unverbindlich und ohne vollständige<br>Bewerbungsunterlagen.</p>
  </main>
</body>
</html>
```